Superfood Organic Powder needs a new Standup Pouch Design

Superfood brand needs a new package design Standup pouch

We need a new packaging design
*Standup Pouch*
for a NEW superfood product to our brand PureLeafy.

This product is a superfood blend of organic powders such as spiralina, chlorella, wheatgrass etc.

The design should be modern with an organic look, - but feel free to play around with it as you wish.

Our first or *older* product is called Vital Blendo, and contains superfood powders like Maca, Moringa, Baobab, Spirulina, Chlorella, Wheatgrass

Find measurements for the standup pouch in the attachments.

We can either go with a

a white standup pouch with a slight opacity to it
(see attached sample I have from my supplier)

or

mat white standup pouch

Or Natural Kraft if

The white pouch with a slight opacity to it so you can see the powder through the pouch. One cool thing about this one is that if we have an area in the design with no colors, not even white, that area will be completely transparent, see picture of the sample pouch we have in the attachments.
In the sample photo the spider is completely transparent.

The Mat white pouch is just a basic white standup pouch with a mat finish.
What ever you think is best for your design you can suggest.

In the future we will create multiple products, each product should have its own color style to distinguish between them - this product should use green Color code as one of the green colors used in the logo. Of course not all colors should have that code, but just the identifier for this product. Please present an idea to showcase this identifier, it could be a thick horizontal or vertical line somewhere on the pouch.

The standup pouch will be digitally printed so we can use all areas of the pouch.

Please provide 3D mockup of the design in order to better get an idea of the design.
Remember that I consider you as the expert so I'm very open to any suggestions regarding this design - in the end the main goal is to attract customers and that is your area of expertise.

Please let me know if you have any questions - thanks in advance

I'm looking forward to working with you.

Here are some links I have found that I think is great designs just to give a little insight to my designs wishes.:

https://www.pinboardly.example/pin/100000000000000001/ https://www.verdanthusk.example/collections/all-superfood-products
https://www.pinboardly.example/pin/100000000000000002/
https://designduel.example/product-label-design/contests/print-design-stand-up-resealable-pouch-organic-spice-100003
https://www.pinboardly.example/pin/100000000000000004/
https://www.pinboardly.example/pin/10000000000000005/
https://www.pinboardly.example/pin/100000000000000006/
https://www.pinboardly.example/pin/100000000000000007/ https://www.pinboardly.example/pin/100000000000000008/
https://www.pinboardly.example/pin/10000000000000009/

Reason: Needed more work because I changed manufacturer of standup pouches.

Target Market(s)

Vegans, Organic interested clients, healthy living, Fitness, Juicers

Industry/Entity Type

Health And Wellness

Requirements
Must have
• The following text should be added on front of the label under the product name:
• Danish certified organic
• Superfood blend
• —
• The product contains the following ingredients and should be mentioned on the front - only the ingredients names:
• Maca, Moringa, Baobab, Spirulina, Chlorella, Wheatgrass
• —
• Organic logo:
• Organic EU logo should be present on the back (find logo in the attachments) To the right of the logo the following text is mandatory with Myriad Pro Regular as a type-font: See previous design for instructions.
• "EU-LOGO-HERE"
• DK-ØKO-000
• EU/ikke-EU-jordbrug
• EU/non-EU Agriculture
• Next to the EU organic logo we will place the danish organic logo which is attached as well, you can decide if it should be on the left or right side, it is a red Ø logo ( find in the attachments as well.
• —
• The label should contain a Nutritional Information with the danish language as primary. By law in Denmark the language used should be danish but it is allowed to add the English word after the danish separated by a /
• So it should be titled as Næringsindhold / Nutritional information (Title Bold font)
• And contain the following:
• energi (KJ/kcal)
• • fedt / fat (g)
• • - heraf mættede fedtsyrer / from saturated fat (g)
• • kulhydrat / carbohydrates (g)
• • - heraf sukkerarter / from sugar (g)
• • protein (g)
• • salt (g)
• • kostfibre / dietary fiber (g)
• —
• We need ingredients list on the back as well titled Ingredienser / Ingredients (Title Bold font)
• Maca, Moringa, Baobab, Spirulina, Chlorella, Hvedegræs / Wheatgrass
• Nettovægt / Netto weight 225 gr
• —-
• You can add some cool logos indicating that the product is:
• 100 % organic
• 100% vegan
• No additives
• Non-GMO
• Gluten free
• —
• Instructions (Title Bold font)
• Mix the superfood powder into 250 ml water with a twist of lemon, coconut water, green juice, smoothies, almond milk, or add to your favorit morning meal.
• Serving size 1-2 teaspoon
• Would be great with 3-4 images describing the instructions
• Image 1 could be fruit being put in a blender
• Image 2 could be 1 teaspoon with powder on top of a blender
• Image 3 could be a blender in use
• Image 4 poring the smoothie in to a glass to enjoy
• —
• Opbevaring / Storage (Title Bold font)
• Opbevares tørt og ikke for varmt
• Keep in a cool and dry place away from sunlight
• —
• Batch: (Title Bold font)
• Best before / Bedst før: (Title Bold font)
• —
• Barcode field
• Make room for a barcode
• —
• Produced in EU for: (Title Bold font)
• Kornvik IVS
• Tranebærvej 42
• 8960 Randers SØ
• Denmark
• www.pureleafy-shop.example (make this bold as well)
• —
• Follow us (Title Bold font)
• Instagram and facebook logo on the back with hashtag #pureleafyshop
• —
• Other than that pureleafy logo can be added as well, it is attached as well.
• I will attach our logo with original AI files.
• —
• Our mission (text)
• We want to provide our customers with the best possible superfood blends. Allowing our customers to get a product packed with antioxidants, vitamins and minerals to elevate their health to the next level. All our products are vegan friendly and GMO free - produced under the best possible circumstances.
• —
Nice to have
• Green color from the logo can be used to get it streamlined.
• Color code c2ce48

```html
<!DOCTYPE html>
<html lang="en">
<head>
<meta charset="utf-8">
<title>PureLeafy – Vital Blendo Standup Pouch</title>
<link rel="stylesheet" href="https://fonts.googleapis.com/css2?family=Montserrat:wght@300;400;500;800&family=Raleway:wght@400;500&family=Parisienne&family=Oswald:wght@500&display=swap">
<style>
  :root {
    --bg: #e4e4e4;
    --pouch: #f7f7f7;
    --seam: #dedede;
    --brand-green: #1e9a2c;
    --lime: #c2ce48;
    --panel: #b9c824;
    --panel-text: #ffffff;
    --panel-soft: #f3f7c8;
    --leaf-light: #a9c22a;
    --leaf-dark: #5f9a1c;
  }
  * { box-sizing: border-box; margin: 0; padding: 0; }
  html, body { width: 1200px; height: 1147px; overflow: hidden; }
  body {
    background: radial-gradient(ellipse at 50% 40%, #f2f2f2 0%, var(--bg) 75%);
    font-family: "Montserrat", sans-serif;
    position: relative;
  }
  .pouch {
    position: absolute;
    left: 280px; top: 88px;
    width: 640px; height: 970px;
    background: var(--pouch);
    border: 24px solid var(--seam);
    border-bottom-width: 0;
    border-radius: 4px 4px 10px 10px;
    box-shadow: 0 18px 40px rgba(0,0,0,.12);
  }
  .pouch__inner { position: absolute; inset: 0; }
  .zip-line {
    position: absolute; left: 0; right: 0; top: 100px;
    height: 10px; border-top: 2px solid #e6e6e6; border-bottom: 2px solid #ececec;
  }
  .leaf-column {
    position: absolute; left: 46px; top: 0;
    width: 220px; height: 946px;
  }
  .brand {
    position: absolute; left: 330px; top: 250px; width: 262px;
    display: flex; align-items: center; gap: 10px;
  }
  .brand__dot { width: 26px; height: 26px; border-radius: 50%; background: var(--lime); flex: none; }
  .brand__name { font-size: 40px; font-weight: 500; color: var(--brand-green); letter-spacing: 1px; }
  .rule {
    position: absolute; left: 330px; top: 382px; width: 262px;
    height: 2px; background: var(--brand-green);
  }
  .claim { position: absolute; left: 330px; top: 410px; width: 262px; text-align: center; color: var(--brand-green); }
  .claim__line { font-family: "Raleway", sans-serif; font-size: 22px; font-weight: 500; letter-spacing: .3px; }
  .claim__big { font-size: 44px; font-weight: 400; line-height: 1.05; letter-spacing: .5px; }
  .claim__script {
    font-family: "Parisienne", cursive; font-size: 24px; color: #2a4a1a;
    display: flex; align-items: center; justify-content: center; gap: 6px;
  }
  .claim__script::before, .claim__script::after {
    content: ""; width: 22px; height: 8px; border-radius: 50%; background: var(--brand-green);
  }
  .product-panel {
    position: absolute; left: 310px; top: 562px; right: -24px; height: 282px;
    background: var(--panel);
    border-radius: 16px 0 0 16px;
    padding: 28px 24px 0 36px;
    color: var(--panel-text);
  }
  .product-name__top { font-size: 60px; font-weight: 800; line-height: 1; letter-spacing: 1px; }
  .product-name__bottom { font-size: 52px; font-weight: 300; line-height: 1.1; letter-spacing: 1px; }
  .dots { border-top: 2px dotted rgba(255,255,255,.85); margin: 12px 0 0; width: 264px; }
  .claims-row { display: flex; width: 264px; padding: 10px 0 8px; }
  .claims-row__item {
    flex: 1; text-align: center; border-left: 1px solid rgba(255,255,255,.85);
    font-size: 10px; line-height: 1.4;
  }
  .claims-row__item:first-child { border-left: 0; text-align: left; }
  .claims-row__item strong { display: block; font-size: 13px; font-weight: 500; color: var(--panel-soft); }
  .ingredients {
    margin-top: 20px; font-family: "Oswald", sans-serif; font-size: 10.5px;
    letter-spacing: .4px; line-height: 1.45; text-transform: uppercase; color: var(--panel-soft);
  }
  .cert-badge {
    position: absolute; right: 36px; bottom: 48px;
    width: 34px; height: 34px; border-radius: 50%; background: #6fb53a; border: 2px solid #fff;
  }
</style>
</head>
<body>
  <div class="pouch">
    <div class="pouch__inner">
      <div class="zip-line"></div>

      <svg class="leaf-column" viewBox="0 0 220 946" role="img" aria-label="Column of stylised green leaves, some patterned and some filled with powder texture, falling down the left side of the pouch">
        <defs>
          <linearGradient id="leafFade" x1="0" y1="0" x2="0" y2="1">
            <stop offset="0" stop-color="var(--leaf-light)" stop-opacity=".85"/>
            <stop offset=".5" stop-color="var(--leaf-dark)" stop-opacity=".9"/>
            <stop offset="1" stop-color="var(--leaf-light)" stop-opacity=".85"/>
          </linearGradient>
        </defs>
        <rect x="0" y="0" width="220" height="946" rx="100" fill="url(#leafFade)" opacity=".55"/>
      </svg>

      <div class="brand">
        <span class="brand__dot"></span>
        <span class="brand__name">PureLeafy</span>
      </div>
      <div class="rule"></div>

      <div class="claim">
        <p class="claim__line">DANISH CERTIFIED</p>
        <p class="claim__big">ORGANIC</p>
        <p class="claim__script">Superfood Blend</p>
      </div>

      <section class="product-panel">
        <h1 class="product-name">
          <span class="product-name__top">VITAL</span><br>
          <span class="product-name__bottom">BLENDO</span>
        </h1>
        <div class="dots"></div>
        <div class="claims-row">
          <div class="claims-row__item"><strong>100 %</strong>Organic</div>
          <div class="claims-row__item"><strong>100 %</strong>Vegan</div>
          <div class="claims-row__item"><strong>NO</strong>Additives</div>
          <div class="claims-row__item"><strong>NON</strong>GMO</div>
        </div>
        <div class="dots"></div>
        <p class="ingredients">Maca, Moringa, Baobab,<br>Spirulina, Chlorella, Wheatgrass</p>
        <span class="cert-badge"></span>
      </section>
    </div>
  </div>
</body>
</html>
```